Web design required

1-We need a web design for existing company based in New Zealand
2-We build residential house and light commercial
3-We has in-house designer which allow us can provide interior design
4-We modeling project before site construction, which enable both client and construction team to visually analysis whole project,

Target Market(s)

middle class residential house market
Ref: http://www.parvellbuilders.co.nz/

Industry/Entity Type

Construction Company

Number of Pages Required

1 page

Font styles to use
Sans Serif
Other font styles liked:
• Such as : Central Gothic or similar which has more design taste

Colors

Designer to choose colors to be used in the design.

Requirements
Must have
• Front sheet, contact information, sample project

```html
<!DOCTYPE html>
<html lang="en">
<head>
<meta charset="utf-8">
<title>Kestrel Homes</title>
<link href="https://fonts.googleapis.com/css2?family=Montserrat:wght@400;600&family=Questrial&family=Open+Sans:wght@400&display=swap" rel="stylesheet">
<style>
:root{
  --blue:#0b68b0;
  --blue-band:#0d67b0;
  --ink:#1c1c1c;
  --grey:#8a8a8a;
  --white:#ffffff;
  --line:#bdbdbd;
  --shade:rgba(8,10,14,.55);
}
*{margin:0;padding:0;box-sizing:border-box}
html,body{width:1200px;height:2479px;overflow:hidden}
body{position:relative;background:var(--white);font-family:"Questrial",sans-serif;color:var(--ink)}
.photo{position:absolute}
.label-shade{position:absolute;background:linear-gradient(180deg,rgba(0,0,0,0) 0%,var(--shade) 100%)}

/* hero */
.hero{position:absolute;left:0;top:0;width:1200px;height:620px;overflow:hidden}
.brand{position:absolute;left:88px;top:26px;display:flex;align-items:center;gap:16px}
.brand-dot{width:70px;height:70px;border-radius:50%;background:var(--white)}
.brand-name{font-family:"Montserrat",sans-serif;font-weight:600;font-size:28px;letter-spacing:5px;color:var(--white);line-height:1}
.nav{position:absolute;top:40px;left:617px;font-size:15px;color:var(--white)}
.nav a{color:var(--white);text-decoration:none;position:absolute;top:0;line-height:36px;white-space:nowrap}
.nav .current{border:1.5px solid var(--white);padding:0 24px}
.project-label{position:absolute;left:655px;top:528px;font-size:23px;color:var(--white)}

/* about */
.about{position:absolute;left:0;top:620px;width:1200px;height:554px;overflow:hidden}
.about-kicker{position:absolute;left:88px;top:92px;font-size:22px;letter-spacing:8px;color:var(--ink)}
.about-title{position:absolute;left:88px;top:130px;font-family:"Montserrat",sans-serif;font-size:29px;letter-spacing:7px;color:var(--blue)}
.about-title b{font-weight:600}
.about-title span{font-weight:400}
.about-copy{position:absolute;left:88px;top:186px;width:540px;font-size:16px;line-height:26px;letter-spacing:1.6px;color:var(--grey)}
.about-copy p+p{margin-top:26px}
.btn{position:absolute;background:var(--blue);color:var(--white);font-size:16px;letter-spacing:1px;display:flex;align-items:center;justify-content:center}

/* services */
.services{position:absolute;left:0;top:1174px;width:1200px;height:554px;overflow:hidden}
.tile-label{position:absolute;font-size:20px;color:var(--white);white-space:nowrap}
.services-kicker{position:absolute;left:84px;top:194px;font-size:22px;letter-spacing:9px;color:var(--white)}
.services-title{position:absolute;left:84px;top:230px;font-family:"Montserrat",sans-serif;font-weight:600;font-size:29px;letter-spacing:7px;color:var(--white)}

/* footer */
.footer{position:absolute;left:0;top:1728px;width:1200px;height:669px;overflow:hidden}
.footer-name{position:absolute;left:86px;top:86px;font-size:30px;color:var(--white)}
.info{position:absolute;left:88px;display:flex;align-items:center;gap:22px;font-size:20px;color:#e2e2e2}
.info svg{width:18px;height:18px;flex:none}
.join{position:absolute;left:88px;top:322px;font-size:21px;color:var(--blue)}
.email-field{position:absolute;left:88px;top:375px;width:309px;height:51px;border:1.5px solid #cfcfcf;color:#a8a8a8;font-size:15px;padding-left:36px;line-height:48px}
.social{position:absolute;top:536px;width:33px;height:33px;border-radius:50%}
.contact-card{position:absolute;left:650px;top:72px;width:463px;height:513px;background:var(--white);border-radius:3px}
.contact-title{position:absolute;left:0;right:0;top:44px;text-align:center;font-size:34px;font-weight:400;color:var(--ink)}
.field{position:absolute;left:34px;width:394px;border-bottom:1.5px solid var(--line);font-size:15px;color:var(--ink);padding-bottom:16px}
.copyright{position:absolute;left:0;top:2397px;width:1200px;height:82px;background:var(--blue-band);color:var(--white);font-family:"Open Sans",sans-serif;font-size:14px;display:flex;align-items:center;justify-content:center}
</style>
</head>
<body>

<header class="hero">
  <div class="photo" role="img" aria-label="Floating timber staircase with warm wood ceiling" style="left:0;top:0;width:455px;height:309px;background:radial-gradient(ellipse at 75% 35%,rgba(170,120,75,.75),rgba(0,0,0,0) 55%),linear-gradient(120deg,#cfc8bf 0%,#8d857c 22%,#3a3531 50%,#2a2624 100%)"></div>
  <div class="photo" role="img" aria-label="Dark timber wall and window frame" style="left:455px;top:0;width:145px;height:309px;background:linear-gradient(90deg,#1a1918,#3a3734 45%,#1d1c1b)"></div>
  <div class="photo" role="img" aria-label="White house facade with garden at night" style="left:600px;top:0;width:600px;height:309px;background:radial-gradient(ellipse at 35% 55%,rgba(200,200,195,.45),rgba(0,0,0,0) 50%),linear-gradient(180deg,#1a1c1f 0%,#2f3235 40%,#3e423f 65%,#1f2420 100%)"></div>
  <div class="photo" role="img" aria-label="Modern dark clad two storey house" style="left:0;top:309px;width:600px;height:311px;background:linear-gradient(180deg,#8a8f94 0%,#5b5f63 30%,#34373a 55%,#1c1d1e 100%)"></div>
  <div class="photo" role="img" aria-label="White weatherboard house with lit windows at dusk" style="left:600px;top:309px;width:600px;height:311px;background:radial-gradient(ellipse at 45% 70%,rgba(235,200,120,.7),rgba(0,0,0,0) 45%),linear-gradient(180deg,#2f5fa6 0%,#5a86c0 25%,#d9dde3 45%,#b9b6ad 65%,#3a3530 100%)"></div>
  <div class="label-shade" style="left:600px;top:480px;width:600px;height:140px"></div>

  <div class="brand"><span class="brand-dot"></span><span class="brand-name">KESTREL</span></div>
  <nav class="nav">
    <a class="current" style="left:0">Home</a>
    <a style="left:117px">Services</a>
    <a style="left:223px">About</a>
    <a style="left:317px">Projects</a>
    <a style="left:419px">Contact Us</a>
  </nav>
  <div class="project-label">Fern Rd Project</div>
</header>

<section class="about">
  <div class="photo" role="img" aria-label="House under construction with scaffolding and fencing" style="left:0;top:0;width:1200px;height:554px;clip-path:polygon(930px 0,1200px 0,1200px 554px,689px 554px);background:linear-gradient(180deg,#5479ad 0%,#9fb0c6 22%,#7c8088 42%,#55595e 62%,#4f6b3a 82%,#3c3c3a 100%)"></div>
  <div class="about-kicker">About</div>
  <h2 class="about-title"><b>KESTREL</b> <span>HOMES</span></h2>
  <div class="about-copy">
    <p>Kestrel Homes is dedicated to creating and renovating beautiful and unusual buildings.</p>
    <p>Kestrel Homes works with you to take dream houses off the blueprints and into reality. We have the knowledge and expertise to customise homes to suit you – from unusual materials and designs to environmentally sensitive locations.</p>
  </div>
  <div class="btn" style="left:88px;top:407px;width:147px;height:51px">Read More &gt;</div>
</section>

<section class="services">
  <div class="photo" role="img" aria-label="Metal roof of a finished home under a stormy sky" style="left:0;top:0;width:1200px;height:554px;background:linear-gradient(180deg,#1f2836 0%,#3a4656 30%,#8b929a 48%,#5d6670 58%,#2f4a2a 72%,#55682f 88%,#6b7a3a 100%)"></div>
  <div class="photo" role="img" aria-label="Hands reviewing construction plans" style="left:0;top:0;width:857px;height:278px;clip-path:polygon(687px 0,857px 0,857px 278px,570px 278px);background:radial-gradient(ellipse at 55% 35%,rgba(230,225,215,.8),rgba(0,0,0,0) 55%),linear-gradient(160deg,#7d7f84,#3c3e42 60%,#1c1d20)"></div>
  <div class="photo" role="img" aria-label="Scale model of a house with tools" style="left:857px;top:0;width:343px;height:278px;background:radial-gradient(ellipse at 60% 45%,rgba(200,110,70,.55),rgba(0,0,0,0) 45%),linear-gradient(180deg,#e6e8ea 0%,#d8d6d2 40%,#c9b49b 62%,#3a3733 100%)"></div>
  <div class="photo" role="img" aria-label="Project managers in hard hats reviewing plans" style="left:0;top:278px;width:857px;height:276px;clip-path:polygon(570px 0,857px 0,857px 276px,433px 276px);background:radial-gradient(ellipse at 70% 40%,rgba(210,215,225,.45),rgba(0,0,0,0) 45%),linear-gradient(160deg,#2d5680,#1f2c3c 55%,#12161c)"></div>
  <div class="photo" role="img" aria-label="Light commercial building with roller doors" style="left:857px;top:278px;width:343px;height:276px;background:linear-gradient(180deg,#3f86cf 0%,#6fa5dd 12%,#b5682f 24%,#c5773c 45%,#d9d6cf 60%,#bdb9b0 80%,#4a4a48 100%)"></div>
  <div class="label-shade" style="left:560px;top:190px;width:640px;height:88px"></div>
  <div class="label-shade" style="left:430px;top:466px;width:770px;height:88px"></div>

  <div class="services-kicker">Our</div>
  <h2 class="services-title">SERVICES</h2>
  <div class="btn" style="left:84px;top:304px;width:147px;height:53px">View More &gt;</div>

  <div class="tile-label" style="left:613px;top:221px">Preconstruction Planning</div>
  <div class="tile-label" style="left:906px;top:221px">Construction Modelling</div>
  <div class="tile-label" style="left:612px;top:496px">Full Project Management</div>
  <div class="tile-label" style="left:955px;top:496px">Light Commercial</div>
</section>

<footer class="footer">
  <div class="photo" role="img" aria-label="Darkened photo of a house under construction" style="left:0;top:0;width:1200px;height:669px;background:radial-gradient(ellipse at 40% 60%,rgba(70,85,105,.45),rgba(0,0,0,0) 60%),linear-gradient(180deg,#10151c,#1e2631 50%,#0f1318)"></div>
  <div class="footer-name">Kestrel Homes</div>
  <div class="info" style="top:164px">
    <svg viewBox="0 0 18 18"><path d="M9 1a6 6 0 0 0-6 6c0 4.5 6 10 6 10s6-5.5 6-10a6 6 0 0 0-6-6zm0 8.3A2.3 2.3 0 1 1 9 4.7a2.3 2.3 0 0 1 0 4.6z" fill="#e2e2e2"/></svg>
    <span>18 Harbourview Lane, Riverside Auckland.</span>
  </div>
  <div class="info" style="top:212px">
    <svg viewBox="0 0 18 18"><path d="M4 1.5l3 3-1.8 2.2a10 10 0 0 0 6 6L13.5 11l3 3-2 2.5C8 16 2 10 1.5 3.5z" fill="#e2e2e2"/></svg>
    <span>Tel: 0064 9 000 4182</span>
  </div>
  <div class="info" style="top:257px">
    <svg viewBox="0 0 18 18"><rect x="1" y="3.5" width="16" height="11" fill="#e2e2e2"/><path d="M1 4l8 6 8-6" stroke="#161b22" stroke-width="1.5" fill="none"/></svg>
    <span>E-mail: info@kestrelhomes.example</span>
  </div>
  <div class="join">Join the community!</div>
  <div class="email-field">Email Address</div>
  <div class="btn" style="left:88px;top:441px;width:224px;height:55px;font-size:21px;letter-spacing:0">SUBMIT</div>
  <span class="social" style="left:86px;background:#3b5998"></span>
  <span class="social" style="left:125px;background:#3a9ad9"></span>
  <span class="social" style="left:164px;background:#d9342b"></span>
  <span class="social" style="left:203px;background:#c4302b"></span>
  <span class="social" style="left:242px;background:#b23a8c"></span>

  <div class="contact-card">
    <h3 class="contact-title">Contact us</h3>
    <div class="field" style="top:112px">Name</div>
    <div class="field" style="top:193px">Phone</div>
    <div class="field" style="top:274px">Email</div>
    <div class="field" style="top:353px">Message...</div>
    <div class="btn" style="left:253px;top:433px;width:182px;height:58px;font-size:21px;letter-spacing:0">SUBMIT</div>
  </div>
</footer>

<div class="copyright">Copyright (c) 2017. Kestrel Homes. All rights reserved.</div>

</body>
</html>
```